Roofing Contractor business card redesign

I want to redesign my business card with a fresh, eye catching concept

Target Market(s)

Residential Roofing Clients, potential employees, and subcontractors.

Industry/Entity Type

Business

Colors

Designer to choose colors to be used in the design.

Requirements
Nice to have
• I just want something that's more pleasing to the eye. You can use a combination of either / or of my logos.

```html
<!DOCTYPE html>
<html lang="en">
<head>
<meta charset="utf-8">
<title>Fair Hands General Contractors — Business Card</title>
<link rel="stylesheet" href="https://fonts.googleapis.com/css2?family=Open+Sans:wght@400;600;700;800&display=swap">
<style>
  :root {
    --stage: #5b5b5b;
    --paper: #ffffff;
    --brown: #4a1410;
    --orange: #e8761f;
    --ink: #2b2b2b;
    --yellow-light: #fbe45a;
    --yellow: #f6cb1e;
    --yellow-deep: #f4b60f;
    --seal-tone: #d9d2c8;
  }
  * { margin: 0; padding: 0; box-sizing: border-box; }
  html, body { width: 1200px; height: 1200px; overflow: hidden; }
  body {
    background: var(--stage);
    font-family: "Open Sans", Arial, sans-serif;
    position: relative;
  }
  .card {
    position: absolute;
    left: 150px;
    width: 900px;
    height: 508px;
    overflow: hidden;
    box-shadow: 0 10px 30px rgba(0,0,0,.35);
  }
  .card--front { top: 61px; background: var(--paper); }
  .card--back {
    top: 631px;
    background: linear-gradient(160deg, var(--yellow-light) 0%, var(--yellow) 45%, var(--yellow-deep) 100%);
  }

  /* front */
  .brand-seal {
    position: absolute; left: 44px; top: 31px;
    width: 156px; height: 156px; border-radius: 50%;
    background: radial-gradient(circle at 50% 45%, #f0a040 0%, #b8541c 55%, var(--brown) 100%);
    border: 8px solid var(--brown);
  }
  .faint-seal {
    position: absolute; left: 600px; top: -10px;
    width: 320px; height: 320px; border-radius: 50%;
    background: var(--seal-tone); opacity: .3;
  }
  .brand-name {
    position: absolute; left: 229px; top: 54px;
    font-weight: 800; font-size: 54px; line-height: 1;
    color: var(--brown); letter-spacing: -1.5px;
  }
  .brand-sub {
    position: absolute; left: 231px; top: 131px;
    font-weight: 700; font-size: 20px; line-height: 26px; color: var(--brown);
  }
  .person-name {
    position: absolute; left: 229px; top: 175px;
    font-weight: 600; font-size: 42px; line-height: 56px; color: var(--brown);
  }
  .person-titles {
    position: absolute; left: 231px; top: 229px;
    font-size: 23px; line-height: 30px; color: var(--orange);
    text-transform: uppercase;
  }
  .contact-list {
    position: absolute; left: 231px; top: 304px;
    list-style: none; font-size: 26px; line-height: 35px; color: var(--ink);
  }
  .contact-list li { display: flex; align-items: center; gap: 12px; }
  .contact-list svg { width: 22px; height: 22px; fill: var(--orange); flex: none; }

  /* back */
  .back-tone {
    position: absolute; inset: 0;
    background: radial-gradient(ellipse at 30% 10%, rgba(255,240,140,.55) 0%, rgba(255,240,140,0) 60%);
  }
  .back-lockup {
    position: absolute; left: 0; right: 0; top: 156px;
    display: flex; align-items: center; justify-content: center; gap: 14px;
  }
  .back-seal {
    width: 156px; height: 156px; border-radius: 50%; flex: none;
    background: radial-gradient(circle at 50% 45%, #f0a040 0%, #b8541c 55%, var(--brown) 100%);
    border: 8px solid var(--brown);
  }
  .back-word {
    font-weight: 800; font-size: 96px; line-height: 1; color: var(--brown); letter-spacing: -2px;
  }
  .back-sub {
    position: absolute; left: 0; right: 0; top: 318px; text-align: center;
    font-weight: 700; font-size: 31px; line-height: 40px; color: var(--brown);
  }
</style>
</head>
<body>

<section class="card card--front">
  <div class="faint-seal" role="img" aria-label="Faint company emblem decoration"></div>
  <div class="brand-seal" role="img" aria-label="Company emblem"></div>
  <div class="brand-name">Fair Hands</div>
  <div class="brand-sub">General Contractors, Inc.</div>
  <div class="person-name">Dale Morrow</div>
  <div class="person-titles">Peakline Certified Roof Inspector<br>Licensed Property Adjuster</div>
  <ul class="contact-list">
    <li><svg viewBox="0 0 24 24"><path d="M7 1h10a2 2 0 0 1 2 2v18a2 2 0 0 1-2 2H7a2 2 0 0 1-2-2V3a2 2 0 0 1 2-2zm0 3v14h10V4z"/></svg>(555) 201-7346</li>
    <li><svg viewBox="0 0 24 24"><path d="M6.6 10.8a15.1 15.1 0 0 0 6.6 6.6l2.2-2.2a1 1 0 0 1 1-.25 11.4 11.4 0 0 0 3.6.57 1 1 0 0 1 1 1V20a1 1 0 0 1-1 1A17 17 0 0 1 3 4a1 1 0 0 1 1-1h3.5a1 1 0 0 1 1 1c0 1.25.2 2.45.57 3.57a1 1 0 0 1-.25 1z"/></svg>(555) 318-9020</li>
    <li><svg viewBox="0 0 24 24"><path d="M2 5h20v14H2zm2 2v.5l8 5 8-5V7z"/></svg>dale@fairhandstx.com</li>
    <li><svg viewBox="0 0 24 24"><path d="M10.6 13.4a1 1 0 0 1 0-1.4l3-3a1 1 0 1 1 1.4 1.4l-3 3a1 1 0 0 1-1.4 0zM5.5 14.5l2.1-2.1 1.4 1.4-2.1 2.1a2 2 0 0 0 2.8 2.8l2.1-2.1 1.4 1.4-2.1 2.1a4 4 0 0 1-5.6-5.6zm13-5l-2.1 2.1-1.4-1.4 2.1-2.1a2 2 0 0 0-2.8-2.8l-2.1 2.1-1.4-1.4 2.1-2.1a4 4 0 0 1 5.6 5.6z"/></svg>www.fairhandsgc.com</li>
    <li><svg viewBox="0 0 24 24"><path d="M12 2a7 7 0 0 1 7 7c0 5-7 13-7 13S5 14 5 9a7 7 0 0 1 7-7zm0 4.5A2.5 2.5 0 1 0 12 11.5 2.5 2.5 0 0 0 12 6.5z"/></svg>4410 Cedar Mill Road Suite, 118 Plano, TX 75093</li>
  </ul>
</section>

<section class="card card--back">
  <div class="back-tone" role="img" aria-label="Soft background illustration of house rooftops and windows"></div>
  <div class="back-lockup">
    <span class="back-word">Fair</span>
    <div class="back-seal" role="img" aria-label="Company emblem"></div>
    <span class="back-word">Hands</span>
  </div>
  <div class="back-sub">General Contractors, Inc.</div>
</section>

</body>
</html>
```